Business Cards - Brightpath Horizon

need to design unique business card for my mortgage business. I need to design credit card style business card for my business or any unique idea that you might have

Target Market(s)

Home Loan customers

Industry/Entity Type

Mortgage Brokerage

Contact Information for Business Card

please design credit card style or very unique style business card

Colors

Designer to choose colors to be used in the design.

Requirements
Must have
• Name
• position
• Phone number
• fax number
• email address
• website address
• social media address
• All above fields will be provided once design in finalised

```html
<!DOCTYPE html>
<html lang="en">
<head>
<meta charset="utf-8">
<title>Brightpath Horizon – Business Card</title>
<link href="https://fonts.googleapis.com/css2?family=Libre+Baskerville&family=Work+Sans:wght@400;500&display=swap" rel="stylesheet">
<style>
  :root {
    --stage: #1d1d20;
    --brand-blue: #2f459c;
    --brand-blue-light: #3d56aa;
    --brand-blue-dark: #26388a;
    --accent-orange: #ef8a1f;
    --paper: #ffffff;
    --ink-soft: #e6e8ef;
  }
  * { box-sizing: border-box; margin: 0; padding: 0; }
  html, body { width: 1200px; height: 963px; overflow: hidden; background: var(--stage); }
  .canvas {
    width: 1200px; height: 963px;
    display: flex; flex-direction: column; align-items: center; justify-content: center; gap: 64px;
  }
  .card {
    position: relative; width: 660px; height: 377px; border-radius: 18px; overflow: hidden;
    box-shadow: 0 14px 36px rgba(0,0,0,.45);
  }
  /* Front */
  .card--front { background: var(--paper); }
  .brand {
    position: absolute; left: 44px; top: 48px;
    display: flex; align-items: center; gap: 12px;
  }
  .brand__mark { width: 16px; height: 16px; background: var(--accent-orange); flex: none; }
  .brand__name {
    font-family: "Libre Baskerville", serif; font-size: 30px; letter-spacing: 1px;
    color: var(--brand-blue); text-transform: uppercase; white-space: nowrap;
  }
  .person { position: absolute; right: 44px; top: 126px; text-align: right; }
  .person__name {
    font-family: "Libre Baskerville", serif; font-size: 22px; letter-spacing: 1px; color: var(--brand-blue);
  }
  .person__role {
    font-family: "Work Sans", sans-serif; font-size: 14px; color: var(--accent-orange); margin-top: 2px;
  }
  .rule {
    position: absolute; left: 44px; right: 44px; top: 180px; height: 1.5px; background: var(--brand-blue);
  }
  .contacts { position: absolute; left: 44px; top: 200px; list-style: none; }
  .contacts li {
    display: flex; align-items: center; gap: 10px;
    font-family: "Work Sans", sans-serif; font-size: 15px; color: var(--brand-blue); line-height: 26px;
  }
  .contacts svg { width: 12px; height: 12px; flex: none; }
  .band { position: absolute; left: 0; bottom: 0; width: 100%; height: 70px; }
  .band svg { position: absolute; inset: 0; width: 100%; height: 100%; }
  .address {
    position: absolute; left: 44px; bottom: 14px;
    font-family: "Work Sans", sans-serif; font-size: 14px; line-height: 20px; color: var(--paper);
  }
  /* Back */
  .card--back {
    background: linear-gradient(135deg, var(--brand-blue-dark), var(--brand-blue-light));
    display: flex; flex-direction: column; align-items: center; justify-content: center;
  }
  .card--back .brand { position: static; }
  .card--back .brand__name { color: var(--ink-soft); font-size: 34px; }
  .website {
    margin-top: 34px; font-family: "Work Sans", sans-serif; font-size: 15px; letter-spacing: 1.5px; color: var(--ink-soft);
  }
</style>
</head>
<body>
<main class="canvas">
  <section class="card card--front" aria-label="Card front">
    <div class="brand">
      <span class="brand__mark"></span>
      <span class="brand__name">Brightpath Horizon</span>
    </div>

    <div class="person">
      <p class="person__name">DANIEL CARVER</p>
      <p class="person__role">Founder</p>
    </div>
    <div class="rule"></div>

    <ul class="contacts">
      <li><svg viewBox="0 0 12 12"><path fill="#ef8a1f" d="M2 1h3l1 3-1.5 1a6 6 0 0 0 2.5 2.5L8 6l3 1v3a1 1 0 0 1-1 1A9 9 0 0 1 1 2a1 1 0 0 1 1-1z"/></svg>555-318-0472</li>
      <li><svg viewBox="0 0 12 12"><path d="M1 2h10v8H1z M1.5 2.5 6 6l4.5-3.5" fill="none" stroke="#ef8a1f" stroke-width="1.3"/></svg>hello@brightpathhome.com</li>
      <li><svg viewBox="0 0 12 12"><circle cx="6" cy="6" r="5" fill="none" stroke="#ef8a1f" stroke-width="1.3"/><path d="M1 6h10M6 1c-3 3-3 7 0 10M6 1c3 3 3 7 0 10" fill="none" stroke="#ef8a1f" stroke-width="1"/></svg>www.brightpathhome.com</li>
    </ul>

    <div class="band">
      <svg viewBox="0 0 660 70" preserveAspectRatio="none"><polygon points="0,0 300,0 360,70 0,70" fill="#2f459c"/></svg>
      <p class="address">480 Harbor View Ave.<br>Lakeside, FL 33410</p>
    </div>
  </section>

  <section class="card card--back" aria-label="Card back">
    <div class="brand">
      <span class="brand__mark"></span>
      <span class="brand__name">Brightpath Horizon</span>
    </div>
    <p class="website">www.yourwebsite.com</p>
  </section>
</main>
</body>
</html>
```